Commercial/Retail/Office Real Estate Lease Brochure for Vacant Space

We need a commercial Real Estate Fyler Template for lease space. We would like it for Vacant lease spaces and new buildings in the commercial, retail, office and industrial lease space. The flyer should have sections for: Highlights (site size, leasable area, Location, Ammenties etc.), concept floor plan or site plan, contact information, project/construction description.

Target Market(s)

Commercial Leasing for Offices and Retail Space

Industry/Entity Type

Real Estate Leasing and Development

Requirements
Must have
• Clean, timeless not overly busy template with spots for key metrics (square feet leaseable space, parking etc), location for pictures
Nice to have
• Marlow Crest Real Estate Logo for header/foot, reusable with adjustments for other spaces
Should not have
• Busy, overall colorfull or contrasting

```html
<!DOCTYPE html>
<html lang="en">
<head>
<meta charset="utf-8">
<title>Marlow Crest – Commercial Leasing Flyer</title>
<link href="https://fonts.googleapis.com/css2?family=Montserrat:wght@400;500;600;700;800;900&display=swap" rel="stylesheet">
<style>
  :root{
    --stage:#7fa9ec;
    --slate:#4a6690;
    --night:#2a3d5e;
    --sky-top:#5f7fa6;
    --sky-mid:#7f98b5;
    --sky-low:#a9bccd;
    --brick:#9a5a3a;
    --panel:#2c3a55;
    --lawn:#55683d;
    --ink:#111111;
    --paper:#ffffff;
    --text:#2b2f36;
    --tick:#5cb83a;
    --white:#ffffff;
  }
  *{margin:0;padding:0;box-sizing:border-box}
  html,body{width:1200px;height:900px;overflow:hidden}
  body{background:var(--stage);font-family:"Montserrat",Arial,sans-serif;position:relative}

  .flyer{position:absolute;top:75px;width:520px;height:750px;overflow:hidden;background:var(--paper);box-shadow:0 14px 30px rgba(20,40,90,.25)}
  .flyer--back{left:60px}
  .flyer--front{left:620px}

  /* features side */
  .features-head{position:absolute;left:0;top:0;width:100%;height:290px;background:var(--slate);overflow:hidden}
  .features-head__photo{position:absolute;right:0;top:0;width:62%;height:100%;
    background:linear-gradient(160deg,#3c5784 0%,var(--night) 55%,#6b5234 100%)}
  .features-head__ghost{position:absolute;left:26px;top:120px;font-size:96px;font-weight:900;letter-spacing:1px;line-height:1;
    color:transparent;-webkit-text-stroke:1px rgba(255,255,255,.28);white-space:nowrap}
  .features-head__kicker{position:absolute;left:34px;top:182px;color:var(--white);font-weight:700;font-size:17px;letter-spacing:.5px}
  .features-head__title{position:absolute;left:30px;top:204px;color:var(--white);font-weight:900;font-size:64px;letter-spacing:1px;line-height:1}

  .feature-list{position:absolute;left:34px;top:318px;right:30px;list-style:none}
  .feature-list li{position:relative;padding-left:22px;margin-bottom:9px;font-size:12.5px;line-height:1.35;color:var(--text);font-weight:500}
  .feature-list svg{position:absolute;left:0;top:2px;width:13px;height:13px}

  .features-fade{position:absolute;left:0;right:0;bottom:58px;height:230px;
    background:linear-gradient(180deg,rgba(255,255,255,1) 0%,rgba(205,205,208,.8) 100%)}

  .contact-bar{position:absolute;left:0;right:0;bottom:0;height:58px;background:var(--ink);color:var(--white);
    display:flex;align-items:center;justify-content:center;gap:22px;font-weight:700;font-size:19px;z-index:2}
  .contact-bar__item{display:flex;align-items:center;gap:8px}
  .contact-bar svg{width:18px;height:18px}

  /* cover side */
  .cover-sky{position:absolute;left:0;right:0;top:0;height:420px;
    background:linear-gradient(180deg,var(--sky-top) 0%,var(--sky-mid) 55%,var(--sky-low) 100%)}
  .cover-building{position:absolute;left:0;right:0;top:380px;bottom:58px;
    background:
      linear-gradient(180deg,rgba(0,0,0,0) 0%,rgba(0,0,0,0) 62%,var(--lawn) 78%,#44532f 100%),
      linear-gradient(90deg,var(--brick) 0%,#7c4a32 38%,var(--panel) 52%,#1f2a40 82%,#8a8f96 100%)}
  .brand{position:absolute;left:0;right:0;top:42px;text-align:center;color:var(--white);z-index:1}
  .brand__name{font-size:46px;font-weight:600;letter-spacing:1px;line-height:1}
  .brand__tagline{font-size:16px;font-weight:400;margin-top:8px;letter-spacing:.5px}
  .cover-title{position:absolute;left:0;right:0;top:160px;text-align:center;color:var(--white);font-weight:900;line-height:1.05;font-size:33px;letter-spacing:1px;z-index:1}
  .cover-sub{position:absolute;left:0;right:0;top:250px;text-align:center;color:var(--white);font-size:13.5px;font-weight:600;letter-spacing:.5px;z-index:1}
</style>
</head>
<body>

<section class="flyer flyer--back">
  <div class="features-head">
    <div class="features-head__photo" role="img" aria-label="Night photograph of the two-storey commercial building with lit facade"></div>
    <div class="features-head__ghost" aria-hidden="true">FEATURES</div>
    <div class="features-head__kicker">PRIME COMMERCIAL SPACE FOR LEASE</div>
    <h2 class="features-head__title">FEATURES</h2>
  </div>

  <div class="features-fade" role="img" aria-label="Faded greyscale photograph of the building facade"></div>

  <ul class="feature-list">
    <li><svg viewBox="0 0 16 16"><circle cx="8" cy="8" r="8" fill="var(--tick)"/><path d="M4.5 8.3l2.3 2.3 4.7-5" stroke="#fff" stroke-width="1.8" fill="none"/></svg>Anchored by Northgate Wholesale &amp; Gas Bar</li>
    <li><svg viewBox="0 0 16 16"><circle cx="8" cy="8" r="8" fill="var(--tick)"/><path d="M4.5 8.3l2.3 2.3 4.7-5" stroke="#fff" stroke-width="1.8" fill="none"/></svg>Current site tenants include Burger Lane, Brewhouse Coffee, Paw &amp; Kibble Co.</li>
    <li><svg viewBox="0 0 16 16"><circle cx="8" cy="8" r="8" fill="var(--tick)"/><path d="M4.5 8.3l2.3 2.3 4.7-5" stroke="#fff" stroke-width="1.8" fill="none"/></svg>Close proximity to Ashford commercial node</li>
    <li><svg viewBox="0 0 16 16"><circle cx="8" cy="8" r="8" fill="var(--tick)"/><path d="M4.5 8.3l2.3 2.3 4.7-5" stroke="#fff" stroke-width="1.8" fill="none"/></svg>Offers fantastic visibility from the Lakeshore Highway</li>
    <li><svg viewBox="0 0 16 16"><circle cx="8" cy="8" r="8" fill="var(--tick)"/><path d="M4.5 8.3l2.3 2.3 4.7-5" stroke="#fff" stroke-width="1.8" fill="none"/></svg>High traffic area with average daily vehicle counts of</li>
    <li><svg viewBox="0 0 16 16"><circle cx="8" cy="8" r="8" fill="var(--tick)"/><path d="M4.5 8.3l2.3 2.3 4.7-5" stroke="#fff" stroke-width="1.8" fill="none"/></svg>325,000 vehicles daily at the intersection of Slate Road</li>
    <li><svg viewBox="0 0 16 16"><circle cx="8" cy="8" r="8" fill="var(--tick)"/><path d="M4.5 8.3l2.3 2.3 4.7-5" stroke="#fff" stroke-width="1.8" fill="none"/></svg>Drive (43% increase since Northgate Wholesale has opened)</li>
    <li><svg viewBox="0 0 16 16"><circle cx="8" cy="8" r="8" fill="var(--tick)"/><path d="M4.5 8.3l2.3 2.3 4.7-5" stroke="#fff" stroke-width="1.8" fill="none"/></svg>323,300 vehicles daily on the Lakeshore Highway</li>
    <li><svg viewBox="0 0 16 16"><circle cx="8" cy="8" r="8" fill="var(--tick)"/><path d="M4.5 8.3l2.3 2.3 4.7-5" stroke="#fff" stroke-width="1.8" fill="none"/></svg>From 1,315 - 48,200 SF available for lease</li>
    <li><svg viewBox="0 0 16 16"><circle cx="8" cy="8" r="8" fill="var(--tick)"/><path d="M4.5 8.3l2.3 2.3 4.7-5" stroke="#fff" stroke-width="1.8" fill="none"/></svg>3 points of access to Slate Centre from the Lakeshore Highway</li>
    <li><svg viewBox="0 0 16 16"><circle cx="8" cy="8" r="8" fill="var(--tick)"/><path d="M4.5 8.3l2.3 2.3 4.7-5" stroke="#fff" stroke-width="1.8" fill="none"/></svg>Minutes from Riverbend Industrial Park which has over 6,000,000 SF / 3,700 employees</li>
  </ul>

  <footer class="contact-bar">
    <span class="contact-bar__item"><svg viewBox="0 0 24 24"><circle cx="12" cy="12" r="11" fill="none" stroke="#fff" stroke-width="1.6"/><path d="M8.5 6.5c-.8.6-1.2 1.8-.6 3.4 1 2.6 3.2 4.8 5.8 5.8 1.6.6 2.8.2 3.4-.6l-2-2-1.6.9c-1.2-.6-2.2-1.6-2.8-2.8l.9-1.6z" fill="#fff"/></svg>01 5550 1234</span>
    <span class="contact-bar__item"><svg viewBox="0 0 24 24"><circle cx="12" cy="12" r="10" fill="none" stroke="#fff" stroke-width="1.6"/><ellipse cx="12" cy="12" rx="4.5" ry="10" fill="none" stroke="#fff" stroke-width="1.4"/><path d="M2 12h20M4 7h16M4 17h16" stroke="#fff" stroke-width="1.2"/></svg>www.marlowcrest.example</span>
  </footer>
</section>

<section class="flyer flyer--front">
  <div class="cover-sky" role="img" aria-label="Cloudy blue sky above the building"></div>
  <div class="cover-building" role="img" aria-label="Rendering of a modern two-storey office building with a brick wing, dark glazed panels, a parked car and a landscaped lawn in front"></div>
  <div class="brand">
    <div class="brand__name">MARLOW CREST</div>
    <div class="brand__tagline">sustainable architecture + design</div>
  </div>
  <h1 class="cover-title">REAL ESTATE<br>LEASING &amp; DEVELOPMENT</h1>
  <p class="cover-sub">COMMERCIAL LEASING FOR OFFICES &amp; RETAIL SPACE</p>

  <footer class="contact-bar">
    <span class="contact-bar__item"><svg viewBox="0 0 24 24"><circle cx="12" cy="12" r="11" fill="none" stroke="#fff" stroke-width="1.6"/><path d="M8.5 6.5c-.8.6-1.2 1.8-.6 3.4 1 2.6 3.2 4.8 5.8 5.8 1.6.6 2.8.2 3.4-.6l-2-2-1.6.9c-1.2-.6-2.2-1.6-2.8-2.8l.9-1.6z" fill="#fff"/></svg>01 5550 1234</span>
    <span class="contact-bar__item"><svg viewBox="0 0 24 24"><circle cx="12" cy="12" r="10" fill="none" stroke="#fff" stroke-width="1.6"/><ellipse cx="12" cy="12" rx="4.5" ry="10" fill="none" stroke="#fff" stroke-width="1.4"/><path d="M2 12h20M4 7h16M4 17h16" stroke="#fff" stroke-width="1.2"/></svg>www.marlowcrest.example</span>
  </footer>
</section>

</body>
</html>
```